Building company buisness cards

We are looking for a sharp modern new look for our business cards.
We are a New Zealand based company that specialises in house and land packages.
We have attached a photo of the current logo and would like to see if it can be improved somehow if needed.
We are open to any colours but we have chosen green at this stage.
Feel free to change the font and make the logo smarter looking.
Play with the colours and see what looks best.

We want a card that looks so good know one will want to throw it away!

Target Market(s)

Home buyers

Industry/Entity Type

Building

Contact Information for Business Card

Derek Tolvane
0217394062
dtolvane@quillmarkhomesteads.co.nz
quillmarkhomesteads.co.nz

Font styles to use
Serif
Sans Serif

Colors

Designer to choose colors to be used in the design.

Requirements
Must have
• Logo and company name on one side, details on the other side
Nice to have
• Color codes for the original green are HEX #4a8028, RGB(74,128,40), CMYK(42,0,69,50)
• Round corners, Raised and/or spot UV

```html
<!DOCTYPE html>
<html lang="en">
<head>
<meta charset="utf-8">
<title>Quillmark Homesteads – Business Cards</title>
<link rel="stylesheet" href="https://fonts.googleapis.com/css2?family=Open+Sans:wght@400;700&family=Roboto:wght@400;500&display=swap">
<style>
  :root {
    --stage: #2b2b2b;
    --brand-green: #4a8028;
    --roof-grey: #5a5a5a;
    --card-white: #ffffff;
    --name-white: #eeeeee;
    --text-grey: #555555;
  }
  html, body {
    margin: 0;
    padding: 0;
    width: 1125px;
    height: 1200px;
    overflow: hidden;
    background: var(--stage);
  }
  .sheet {
    position: relative;
    width: 1125px;
    height: 1200px;
  }
  .card {
    position: absolute;
    left: 150px;
    width: 826px;
    height: 470px;
    border-radius: 26px;
    overflow: hidden;
  }
  .card--front { top: 98px; background: var(--card-white); }
  .card--back  { top: 631px; background: var(--brand-green); }

  .roof-art {
    position: absolute;
    inset: 0;
    width: 100%;
    height: 100%;
  }
  .holder-name {
    position: absolute;
    top: 38px;
    right: 47px;
    margin: 0;
    font-family: "Roboto", sans-serif;
    font-weight: 500;
    font-size: 28px;
    letter-spacing: 0.5px;
    color: var(--name-white);
    text-transform: uppercase;
  }
  .wordmark {
    position: absolute;
    left: 0;
    right: 0;
    margin: 0;
    text-align: center;
    font-family: "Open Sans", sans-serif;
    font-weight: 700;
    letter-spacing: -0.5px;
  }
  .card--front .wordmark {
    top: 258px;
    font-size: 46px;
    color: var(--brand-green);
  }
  .card--back .wordmark {
    top: 200px;
    font-size: 50px;
    color: var(--card-white);
  }
  .contact {
    position: absolute;
    left: 0;
    right: 0;
    top: 372px;
    margin: 0;
    text-align: center;
    font-family: "Roboto", sans-serif;
    font-weight: 400;
    font-size: 18.5px;
    line-height: 29px;
    color: var(--text-grey);
  }
  .contact span { display: block; }
</style>
</head>
<body>
<main class="sheet">
  <section class="card card--front" aria-label="Card front with contact details">
    <svg class="roof-art" viewBox="0 0 800 456" preserveAspectRatio="none" aria-hidden="true">
      <rect width="800" height="456" fill="var(--roof-grey)"/>
      <polygon points="0,262 400,45 800,255 800,456 0,456" fill="var(--brand-green)"/>
      <polyline points="0,259 400,42 800,252" fill="none" stroke="var(--card-white)" stroke-width="2"/>
      <polygon points="0,292 400,72 800,285 800,456 0,456" fill="var(--card-white)"/>
    </svg>
    <h1 class="holder-name">Derek Tolvane</h1>
    <p class="wordmark">Quillmark Homesteads</p>
    <p class="contact">
      <span>P. 0217394062 E. dtolvane@quillmarkhomesteads.co.nz</span>
      <span>quillmarkhomesteads.co.nz</span>
    </p>
  </section>

  <section class="card card--back" aria-label="Card back with company name">
    <p class="wordmark">Quillmark Homesteads</p>
  </section>
</main>
</body>
</html>
```